US company needs luxury product packaging design for a line of hair extensions

What we Need:
Design product packaging for our top of the line hair extension product called Verosina™, the design should have the Verosina™ name,and the head from our Dovetress logo on the box.

Who we are
Our company DoveTress™ is a wholesaler of 100% human hair extensions. We sell the best quality double drawn hair wefts, clip-ins and wigs.

The detailed brief is in the attached word document with examples of packaging we like and we have also uploaded our company logo

The winning designer(s) will work with us on 9 other products packages that we need, so it is important to think strategically

Thanks

Target Market(s)

African American Women

Industry/Entity Type

Hair And Beauty

Font styles to use
Serif
Decorative
Script

Colors
fbf289
b768aa
e24096
000000
fbd4d5
f59195
ffc214
d3a5cc
eda3c7

Requirements
Must have
• Evoke luxury
Nice to have
• See Attached brief

```html
<!DOCTYPE html>
<html lang="en">
<head>
<meta charset="utf-8">
<title>Verosina Hair Care Tag</title>
<link rel="stylesheet" href="https://fonts.googleapis.com/css2?family=Questrial&display=swap">
<style>
  :root {
    --page-bg: #efece6;
    --gold-edge: #cf8f14;
    --gold-mid: #e3b43a;
    --gold-light: #f3e9a4;
    --ink: #141008;
    --grommet-dark: #3a3a3c;
    --grommet-light: #b9b9bb;
  }
  html, body {
    margin: 0;
    padding: 0;
    width: 1053px;
    height: 1200px;
    overflow: hidden;
    background: var(--page-bg);
  }
  .canvas {
    position: relative;
    width: 1053px;
    height: 1200px;
  }
  .hang-tag {
    position: absolute;
    left: 324px;
    top: 243px;
    width: 404px;
    height: 714px;
    clip-path: polygon(68px 0, 336px 0, 404px 100px, 404px 714px, 0 714px, 0 100px);
    background: linear-gradient(90deg,
      var(--gold-edge) 0%,
      var(--gold-mid) 30%,
      var(--gold-light) 52%,
      var(--gold-mid) 74%,
      var(--gold-edge) 100%);
    font-family: "Questrial", sans-serif;
    color: var(--ink);
  }
  .grommet {
    position: absolute;
    left: 158px;
    top: 61px;
    width: 88px;
    height: 88px;
  }
  .brand {
    position: absolute;
    left: 0;
    width: 100%;
    top: 202px;
    text-align: center;
  }
  .brand-name {
    font-size: 40px;
    line-height: 1;
    letter-spacing: -0.5px;
    text-transform: uppercase;
  }
  .brand-name sup {
    font-size: 10px;
    vertical-align: top;
  }
  .brand-tagline {
    font-size: 11.5px;
    margin-top: 3px;
    padding-left: 8px;
  }
  .care-text {
    position: absolute;
    left: 28px;
    right: 20px;
    font-size: 18px;
    line-height: 21px;
    margin: 0;
  }
  .care-heading { top: 279px; }
  .care-step-1 { top: 314px; }
  .care-step-2 { top: 399px; }
  .care-step-3 { top: 463px; }
  .care-step-4 { top: 548px; }
  .care-step-5 { top: 610px; }
  .maker {
    position: absolute;
    left: 0;
    width: 100%;
    top: 662px;
    display: flex;
    justify-content: center;
    align-items: center;
    gap: 7px;
    font-size: 22px;
    color: #1f2c4a;
  }
  .maker-dot {
    width: 12px;
    height: 12px;
    border-radius: 50%;
    background: #1f2c4a;
  }
</style>
</head>
<body>
<main class="canvas">
  <article class="hang-tag">
    <svg class="grommet" viewBox="0 0 88 88" aria-hidden="true">
      <circle cx="44" cy="44" r="42" fill="var(--grommet-dark)"/>
      <circle cx="44" cy="44" r="36" fill="var(--grommet-light)"/>
      <circle cx="44" cy="44" r="24" fill="var(--grommet-dark)"/>
      <circle cx="44" cy="44" r="20" fill="var(--page-bg)"/>
    </svg>

    <header class="brand">
      <div class="brand-name">Verosina<sup>™</sup></div>
      <div class="brand-tagline">100% Human Hair Extensions</div>
    </header>

    <p class="care-text care-heading">Hair Care Instructions:</p>
    <p class="care-text care-step-1">1. When brushing Verosina, start at the ends and methodically work up towards the root using a weave brush</p>
    <p class="care-text care-step-2">2. Shampoo hair using a mild moisturizing shampoo</p>
    <p class="care-text care-step-3">3. After shampooing, rinse hair thoroughly with warm water and condition with your favorite conditioner</p>
    <p class="care-text care-step-4">4. Blow dry or use any type dryer as you wish</p>
    <p class="care-text care-step-5">5. Style as desired</p>

    <footer class="maker">
      <span class="maker-dot"></span>
      <span class="maker-name">Dovetress</span>
    </footer>
  </article>
</main>
</body>
</html>
```